Professional & attention grabbing.

A business card design, front and back. I already have a logo I will attach, but I am open to something new as well.
Things to include:
Name:
Title:
Phone:
Email:
Wanting something that is professional but attention grabbing.
Also we do a lot of work using drones on natural gas pipelines (leading the future)if you want to include any of that. I'm open to ideas.
Target Market(s)
Natural gas transmission industry / greenhouse gas mitigation industry
Industry/Entity Type
Business
Colors
Designer to choose colors to be used in the design.
Look and feel
Each slider illustrates characteristics of the customer's brand and the style your logo design should communicate.

```html
<!DOCTYPE html>
<html lang="en">
<head>
<meta charset="utf-8">
<title>Veyra Inspections — Business Card, Front and Back</title>
<link rel="stylesheet" href="https://fonts.googleapis.com/css2?family=Roboto:wght@400;700;900&display=swap">
<style>
  :root {
    --page: #e9e8e6;
    --charcoal: #2b2b2b;
    --charcoal-deep: #141414;
    --charcoal-light: #4a4a4a;
    --red: #c8161d;
    --paper: #ffffff;
  }
  * { box-sizing: border-box; margin: 0; padding: 0; }
  html, body {
    width: 1200px; height: 797px; overflow: hidden;
    background: var(--page);
    font-family: "Roboto", Arial, sans-serif;
  }
  .sheet {
    position: relative; width: 1200px; height: 797px;
    display: flex; align-items: center; justify-content: center; gap: 50px;
  }
  .card {
    position: relative; width: 525px; height: 300px;
    background: var(--paper); overflow: hidden;
    box-shadow: 0 6px 18px rgba(0,0,0,.18);
  }

  /* ---------- Front ---------- */
  .front__panel {
    position: absolute; left: 0; top: 0; width: 54%; height: 100%;
    background: linear-gradient(160deg, var(--charcoal-light) 0%, var(--charcoal) 45%, var(--charcoal-deep) 100%);
  }
  .front__top-strip {
    position: absolute; left: 54%; right: 0; top: 0; height: 16px;
    background: linear-gradient(90deg, var(--charcoal) 0%, var(--charcoal-light) 100%);
  }
  .brand {
    position: absolute; display: flex; align-items: center; gap: 12px;
    font-weight: 900; letter-spacing: 1px; text-transform: uppercase;
    white-space: nowrap;
  }
  .brand__square { width: 22px; height: 22px; background: var(--red); flex: none; }
  .front .brand { left: 40px; top: 138px; color: var(--paper); font-size: 44px; line-height: 1; }
  .front__band {
    position: absolute; left: 0; top: 252px; width: 64%; height: 24px;
    background: var(--red);
    clip-path: polygon(0 0, 100% 0, 94% 100%, 0 100%);
    color: var(--paper); font-weight: 700; font-size: 14px;
    line-height: 24px; padding-left: 18px; letter-spacing: .2px;
    white-space: nowrap;
  }
  .front__heading {
    position: absolute; right: 62px; top: 56px; text-align: right;
    color: var(--red); font-weight: 700; font-size: 19px; line-height: 1.05;
    text-transform: uppercase; letter-spacing: .5px;
  }
  .contact {
    position: absolute; right: 62px; text-align: right;
    color: var(--red); font-size: 11px; line-height: 1.25; white-space: nowrap;
  }
  .contact--phone { top: 114px; letter-spacing: .6px; }
  .contact--email { top: 164px; text-transform: uppercase; }
  .contact--sector { top: 192px; }
  .tabs {
    position: absolute; right: 0; top: 106px; width: 44px;
    display: flex; flex-direction: column; gap: 6px;
  }
  .tab {
    position: relative; height: 22px; width: 44px;
    background: var(--charcoal);
    clip-path: polygon(18% 0, 100% 0, 100% 100%, 0 100%);
  }
  .tab__face {
    position: absolute; left: 10px; top: 0; right: 0; bottom: 0;
    background: var(--red);
    clip-path: polygon(22% 0, 100% 0, 100% 100%, 0 100%);
    display: flex; align-items: center; justify-content: center;
  }
  .tab svg { width: 12px; height: 12px; fill: var(--paper); }

  /* ---------- Back ---------- */
  .back__band {
    position: absolute; left: 0; right: 0;
    background: linear-gradient(90deg, var(--charcoal-deep) 0%, var(--charcoal) 55%, var(--charcoal-light) 100%);
  }
  .back__band--top { top: 0; height: 80px; }
  .back__band--bottom { bottom: 0; height: 82px; }
  .back .brand {
    left: 50%; top: 150px; transform: translate(-50%, -50%);
    color: var(--charcoal); font-size: 40px; gap: 14px;
  }
  .back .brand__square { width: 24px; height: 24px; }
</style>
</head>
<body>
<main class="sheet">

  <section class="card front" aria-label="Business card front">
    <div class="front__panel"></div>
    <div class="front__top-strip"></div>

    <div class="brand">
      <span class="brand__square"></span>
      <span class="brand__name">Veyra</span>
    </div>

    <div class="front__band">Greenhouse gas mitigation industry</div>

    <h1 class="front__heading">Veyra<br>Inspections</h1>
    <p class="contact contact--phone">55501 24680</p>
    <p class="contact contact--email">hello@veyrainspect.com</p>
    <p class="contact contact--sector">Natural gas<br>transmission industry</p>

    <div class="tabs">
      <div class="tab"><div class="tab__face">
        <svg viewBox="0 0 24 24" aria-label="Phone"><path d="M6.6 10.8a15 15 0 0 0 6.6 6.6l2.2-2.2c.3-.3.7-.4 1-.2 1.1.4 2.3.6 3.6.6.6 0 1 .4 1 1V20c0 .6-.4 1-1 1A17 17 0 0 1 3 4c0-.6.4-1 1-1h3.5c.6 0 1 .4 1 1 0 1.3.2 2.5.6 3.6.1.3 0 .7-.2 1z"/></svg>
      </div></div>
      <div class="tab"><div class="tab__face">
        <svg viewBox="0 0 24 24" aria-label="Email"><path d="M2 5h20v14H2z M3.5 6.5 12 13l8.5-6.5" stroke="#c8161d" stroke-width="1.6" fill="#ffffff"/></svg>
      </div></div>
      <div class="tab"><div class="tab__face">
        <svg viewBox="0 0 24 24" aria-label="Location"><path d="M12 2a7 7 0 0 0-7 7c0 5.3 7 13 7 13s7-7.7 7-13a7 7 0 0 0-7-7zm0 9.5A2.5 2.5 0 1 1 12 6.5a2.5 2.5 0 0 1 0 5z"/></svg>
      </div></div>
    </div>
  </section>

  <section class="card back" aria-label="Business card back">
    <div class="back__band back__band--top"></div>
    <div class="brand">
      <span class="brand__square"></span>
      <span class="brand__name">Veyra</span>
    </div>
    <div class="back__band back__band--bottom"></div>
  </section>

</main>
</body>
</html>
```